Every Shelf Set Neatly or ESN Organized needs a business card design. ESN Organized is a professi

We need a business card design that is clean, sharp and conveys a sense of organization. I already have a logo.

Target Market(s)

Families (specifically mothers), small business owners, parents, seniors

Industry/Entity Type

Business

Contact Information for Business Card

My website is www.esnorganized-example.com and my Facebook page is http://www.sociallink-example.com/everyshelfsetneatly. The phone number is 418-552-7094 and I want to be listed as Lorna M. Pelham, Owner

Requirements
Must have
• My logo.

```html
<!DOCTYPE html>
<html lang="en">
<head>
<meta charset="utf-8">
<title>ESN Organized – Business Card</title>
<link rel="stylesheet" href="https://fonts.googleapis.com/css2?family=Open+Sans:wght@400;600;700&display=swap">
<style>
  :root {
    --page-bg: #e9ebee;
    --card-blue: #0a7fdc;
    --card-light: #f4f5f6;
    --text-white: #ffffff;
    --text-soft: #e6f1fb;
  }
  * { margin: 0; padding: 0; box-sizing: border-box; }
  html, body {
    width: 1200px;
    height: 900px;
    overflow: hidden;
    background: var(--page-bg);
    font-family: "Open Sans", Arial, sans-serif;
  }
  .card {
    position: absolute;
    left: 120px;
    top: 154px;
    width: 960px;
    height: 592px;
    background: var(--card-light);
    overflow: hidden;
    box-shadow: 0 10px 30px rgba(0, 0, 0, 0.12);
  }
  .card-shape {
    position: absolute;
    inset: 0;
  }
  .brand {
    position: absolute;
    left: 60px;
    top: 78px;
    width: 420px;
    text-align: center;
    color: var(--text-white);
  }
  .brand-mark {
    width: 30px;
    height: 30px;
    border-radius: 50%;
    background: var(--text-white);
    margin: 0 auto 26px;
  }
  .brand-name {
    font-weight: 400;
    font-size: 32px;
    letter-spacing: 4px;
    text-transform: uppercase;
    line-height: 1.35;
  }
  .owner {
    position: absolute;
    left: 81px;
    top: 322px;
    color: var(--text-white);
  }
  .owner-name {
    font-weight: 700;
    font-size: 33px;
    line-height: 1.2;
  }
  .owner-role {
    font-size: 23px;
    color: var(--text-soft);
    margin-top: 2px;
  }
  .contact-list {
    position: absolute;
    left: 81px;
    top: 426px;
    list-style: none;
    color: var(--text-white);
    font-size: 24px;
  }
  .contact-list li {
    display: flex;
    align-items: center;
    height: 40px;
  }
  .contact-icon {
    width: 20px;
    height: 20px;
    margin-right: 14px;
    fill: var(--text-white);
  }
</style>
</head>
<body>
  <main class="card">
    <svg class="card-shape" viewBox="0 0 960 592" width="960" height="592" aria-hidden="true">
      <path fill="var(--card-blue)"
        d="M0 0 H800 Q930 0 930 130 V190 Q930 230 905 265 L690 560 Q668 592 630 592 H0 Z"/>
    </svg>

    <header class="brand">
      <div class="brand-mark"></div>
      <div class="brand-name">Every Shelf<br>Set Neatly</div>
    </header>

    <section class="owner">
      <h1 class="owner-name">Lorna M. Pelham</h1>
      <p class="owner-role">Owner</p>
    </section>

    <ul class="contact-list">
      <li>
        <svg class="contact-icon" viewBox="0 0 24 24" aria-hidden="true">
          <path d="M6.6 10.8a15.1 15.1 0 0 0 6.6 6.6l2.2-2.2a1 1 0 0 1 1-.25 11.4 11.4 0 0 0 3.6.57 1 1 0 0 1 1 1V20a1 1 0 0 1-1 1A17 17 0 0 1 3 4a1 1 0 0 1 1-1h3.5a1 1 0 0 1 1 1c0 1.25.2 2.45.57 3.6a1 1 0 0 1-.25 1z"/>
        </svg>
        418-552-7094
      </li>
      <li>
        <svg class="contact-icon" viewBox="0 0 24 24" aria-hidden="true">
          <path d="M2 5h20v14H2z M3.5 6.5 12 13l8.5-6.5" fill="var(--text-white)" stroke="var(--card-blue)" stroke-width="1.5"/>
        </svg>
        info@esnorganized-example.com
      </li>
      <li>
        <svg class="contact-icon" viewBox="0 0 24 24" aria-hidden="true">
          <circle cx="12" cy="12" r="10"/>
          <path d="M2 12h20 M12 2c3 3 3 17 0 20 M12 2c-3 3-3 17 0 20" fill="none" stroke="var(--card-blue)" stroke-width="1.4"/>
        </svg>
        www.esnorganized-example.com
      </li>
    </ul>
  </main>
</body>
</html>
```